Premium Business Card for Wealth Creation

Please see attached business card for example.
Happy to look at options like Blue background with Yellow
Target Market(s)
People who want to buy investment property or create wealth
Industry/Entity Type
Investment
Contact Information for Business Card
Tel: 1800 314 579
Mobile: 0417 265 904
Address: Level 1, 64 Carrow Lane Brighton Vic 3186
Name: Martin Feldway
Title: CEO
Website: www.quolvane.com.au
Email: martin@quolvane.com.au
Font styles to use
Sans Serif
Colors
0255a3
fbed22
Requirements
Must have
- Look great

```html
<!DOCTYPE html>
<html lang="en">
<head>
<meta charset="utf-8">
<title>Quolvane Business Card</title>
<link href="https://fonts.googleapis.com/css2?family=Open+Sans:wght@400;700;800&display=swap" rel="stylesheet">
<style>
  :root {
    --brand-blue: #0255a3;
    --band-blue: #2f5fb3;
    --band-blue-light: #4a78c6;
    --brand-yellow: #fbed22;
    --accent-yellow: #e8c52a;
    --soft-cream: #f5ecd0;
    --card-white: #ffffff;
    --card-edge: #eef0f3;
    --stage: #e9eaec;
    --text-blue: #2a4a8c;
  }
  * { margin: 0; padding: 0; box-sizing: border-box; }
  html, body { width: 1200px; height: 780px; overflow: hidden; }
  body {
    background: var(--stage);
    font-family: "Open Sans", Arial, sans-serif;
    display: flex;
    align-items: center;
    justify-content: center;
    gap: 40px;
  }
  .card {
    position: relative;
    width: 540px;
    height: 310px;
    background: linear-gradient(180deg, var(--card-white), var(--card-edge));
    overflow: hidden;
    box-shadow: 0 6px 18px rgba(0,0,0,0.12);
  }
  .card-band {
    position: absolute;
    left: 0; right: 0; bottom: 0;
    background: linear-gradient(180deg, var(--band-blue-light), var(--band-blue));
    border-top: 2px solid var(--accent-yellow);
  }
  .front .card-band { height: 72px; }
  .back .card-band { height: 66px; }

  .brand-dot {
    position: absolute;
    border-radius: 50%;
    background: var(--brand-yellow);
  }
  .front .brand-dot {
    width: 76px; height: 76px;
    left: 28px; top: 200px;
    border: 4px solid var(--card-white);
  }
  .front .soft-circle {
    position: absolute;
    width: 190px; height: 190px;
    right: -40px; top: -70px;
    border-radius: 50%;
    background: var(--soft-cream);
    opacity: 0.8;
  }
  .wordmark {
    font-weight: 800;
    color: var(--brand-blue);
    letter-spacing: 1px;
    line-height: 1;
    white-space: nowrap;
  }
  .front .wordmark {
    position: absolute;
    left: 112px; top: 38px;
    font-size: 44px;
  }
  .contact {
    position: absolute;
    left: 190px; top: 100px;
    color: var(--text-blue);
    font-size: 12.5px;
    line-height: 1.35;
  }
  .contact .person-name {
    font-size: 18px;
    font-weight: 700;
    color: var(--brand-blue);
  }
  .contact .person-title {
    color: var(--accent-yellow);
    font-size: 13px;
    margin-bottom: 4px;
  }
  .contact-line { display: flex; align-items: center; gap: 6px; }
  .contact-icon {
    width: 13px; height: 13px;
    background: var(--accent-yellow);
    flex: none;
  }
  .contact-icon svg { display: block; width: 13px; height: 13px; }
  .address { padding-left: 19px; }

  .back .brand-lockup {
    position: absolute;
    left: 0; right: 0; top: 86px;
    display: flex; align-items: center; justify-content: center;
    gap: 14px;
  }
  .back .brand-dot { position: static; width: 62px; height: 62px; }
  .back .wordmark { font-size: 54px; }
  .website {
    position: absolute;
    left: 22px; bottom: 22px;
    color: var(--card-white);
    font-size: 13px;
  }
</style>
</head>
<body>

  <section class="card front">
    <div class="soft-circle"></div>
    <div class="card-band"></div>
    <div class="brand-dot"></div>
    <div class="wordmark">QUOLVANE</div>
    <div class="contact">
      <div class="person-name">Martin Feldway</div>
      <div class="person-title">CEO</div>
      <div class="address">Level 1, 64 Carrow Lane</div>
      <div class="address">Kelbourne Vic 3207</div>
      <div class="contact-line">
        <span class="contact-icon"><svg viewBox="0 0 13 13"><path d="M4 3 L5.5 3 L6 5 L5 6 Q6 8 7.5 8.5 L8.5 7.5 L10 8 L10 9.5 Q6 10 3.5 5 Z" fill="#fff"/></svg></span>
        1800 314 579
      </div>
      <div class="contact-line">
        <span class="contact-icon"><svg viewBox="0 0 13 13"><rect x="4.5" y="2.5" width="4" height="8" rx="0.8" fill="#fff"/></svg></span>
        0417 265 904
      </div>
      <div class="contact-line">
        <span class="contact-icon"><svg viewBox="0 0 13 13"><rect x="2.5" y="4" width="8" height="5.5" fill="#fff"/><path d="M2.5 4 L6.5 7 L10.5 4" stroke="#e8c52a" stroke-width="0.8" fill="none"/></svg></span>
        martin@quolvane.com.au
      </div>
    </div>
  </section>

  <section class="card back">
    <div class="brand-lockup">
      <div class="brand-dot"></div>
      <div class="wordmark">QUOLVANE</div>
    </div>
    <div class="card-band"></div>
    <div class="website">www.quolvane.com.au</div>
  </section>

</body>
</html>
```